Business Card Design

I am a realtor and i also flip houses. I am CEO and Founder of my business which is Voskell Group LLC which is named after my great uncle who died and i was really close to. He was a wonderful friendly man so i want my business to represent him too. My business works with a lot of different people but i want mainly something to show i am a strong confidant woman who owns there own business. I have a really fun personality so i don't want anything TOO serious or manly. I want the perfect mix. My last two business cards i created are too embarrassing to hand out because they are far too girly and i deal with a lot of millionaire clients. I live out in the Palm Springs California area. I think its very important to show i am a single mom, female with her own business at only 24. I don't want to just be a female that blends in with all of the other serious people but yet i don't want to seem immature. People are telling me to stay away from pinks and purples but i don't want blues and greens because they represent men more. But i won't say no to them if there is a happy medium.

Industry/Entity Type

Realtor

Contact Information for Business Card

Voskell Group, LLC
Corinne Tabb
27358 Halvern Ave, C2 517
Palm Harrow, CA 92391
760-419-6735
Corinnedtabb@mailvane.com

```html
<!DOCTYPE html>
<html lang="en">
<head>
<meta charset="utf-8">
<title>Voskell Group LLC – Business Card</title>
<link href="https://fonts.googleapis.com/css2?family=Electrolize&display=swap" rel="stylesheet">
<style>
  :root {
    --card-bg: #c776b5;
    --bar: #b3e0ec;
    --company: #1a9bab;
    --name: #17996a;
    --address: #d6ec7c;
    --contact: #5a4fb2;
    --icon: #138b8c;
  }
  html, body {
    margin: 0;
    padding: 0;
    overflow: hidden;
    background: var(--card-bg);
  }
  .card {
    position: relative;
    width: 1200px;
    height: 702px;
    background: var(--card-bg);
    overflow: hidden;
    font-family: "Electrolize", sans-serif;
  }
  .bars {
    position: absolute;
    left: 0;
    top: 0;
  }
  .bar { fill: var(--bar); }
  .line {
    position: absolute;
    margin: 0;
    white-space: nowrap;
    line-height: 1;
    font-weight: 400;
  }
  .company {
    left: 516px;
    top: 128px;
    font-size: 50px;
    color: var(--company);
  }
  .person-name {
    left: 592px;
    top: 228px;
    font-size: 46px;
    color: var(--name);
  }
  .address {
    left: 598px;
    font-size: 35px;
    color: var(--address);
  }
  .address-1 { top: 296px; }
  .address-2 { top: 346px; }
  .address-3 { top: 410px; }
  .contact {
    left: 592px;
    font-size: 38px;
    color: var(--contact);
  }
  .phone { top: 550px; }
  .email { top: 622px; left: 599px; font-size: 34px; }
  .icon {
    position: absolute;
    fill: var(--icon);
  }
  .icon-phone { left: 527px; top: 552px; }
  .icon-mail { left: 532px; top: 628px; }
</style>
</head>
<body>
  <main class="card">
    <svg class="bars" width="460" height="702" viewBox="0 0 460 702" aria-hidden="true">
      <rect class="bar" x="0" y="52" width="443" height="27"/>
      <rect class="bar" x="3" y="116" width="345" height="27"/>
      <rect class="bar" x="0" y="192" width="254" height="27"/>
      <rect class="bar" x="0" y="258" width="187" height="27"/>
      <rect class="bar" x="0" y="326" width="128" height="27"/>
      <rect class="bar" x="0" y="401" width="187" height="27"/>
      <rect class="bar" x="0" y="478" width="260" height="27"/>
      <rect class="bar" x="0" y="544" width="355" height="27"/>
      <rect class="bar" x="3" y="619" width="445" height="27"/>
    </svg>

    <h1 class="line company">Voskell Group LLC</h1>
    <h2 class="line person-name">Corinne Tabb</h2>
    <p class="line address address-1">27358 Halvern Ave</p>
    <p class="line address address-2">C2 517 Palm Harrow</p>
    <p class="line address address-3">CA 92391</p>

    <svg class="icon icon-phone" width="46" height="44" viewBox="0 0 24 24" aria-hidden="true">
      <path d="M6.6 10.8c1.4 2.8 3.8 5.1 6.6 6.6l2.2-2.2c.3-.3.7-.4 1-.2 1.1.4 2.3.6 3.6.6.6 0 1 .4 1 1V20c0 .6-.4 1-1 1C10.6 21 3 13.4 3 4c0-.6.4-1 1-1h3.5c.6 0 1 .4 1 1 0 1.3.2 2.5.6 3.6.1.3 0 .7-.2 1L6.6 10.8z"/>
    </svg>
    <p class="line contact phone">760-419-6735</p>

    <svg class="icon icon-mail" width="49" height="36" viewBox="0 0 49 36" aria-hidden="true">
      <path d="M0 0h49v36H0z"/>
      <path d="M2 2l22.5 18L47 2M2 34l16-16M47 34L31 18" fill="none" stroke="#c776b5" stroke-width="2.5"/>
    </svg>
    <p class="line contact email">corinnedtabb@mailvane.com</p>
  </main>
</body>
</html>
```